Looking for a cool, modern Cannabis Jar Label

I want you to come up with a better, modern look for a label.

I need it sized to 4” x 3” - I plan to print directly to label printer.

I want you to use Photoshop and deliver me a layered PSD file that I can edit and modify the information as needed..

The label information will need to include places for:
(1) Strain Name - most important part of label - larger font size than rest - example Kestrel Mist, PLV #7, Juniper Hollow
(2) Pricing - for Gram, 1/8, 1/4, 1/2. and Ounce
(3) Strain Designation (Hybrid, Indica or Sativa) - maybe color coded, different color for Indica v. Sativa, just an idea
(4) THC and CBD percentages - for example 23% THC and 0.05% CBD
(5) Farm name - a place where we can add the name/logo of the business that produced the product. example - Ovenrow Farms

I have attached a simple mockup showing the information.

I have also attached a few samples of labels we like to give you an idea of the look and feel we are going for.

I am wanting a very clean, modern, classy, readable look.The font will use is Gotham Font.

HI Everyone! Thank you for all of your designs. I am requesting an extension because I need more time to give adequate feedback to the designers. Thank you for your participation and all of your efforts! I will be making a decision soon!

• Gotham Font

• Thank you for your designs. I am sorry i have been slow in providing feedback, things have been really busy around here!
• I wanted to give some group general feedback. After reviewing all of the designs, there is a common theme among all of the designs that I would like to see changed.
• I would like to see the per gram pricing more prominent on the label. This is what most people are looking for when they are purchasing the product. So I would like to see this stand out from the other pricing tiers. As I think about it, they don't all need to be grouped together in a line. You could have the Per Gram pricing front and center some where and then the other pricing tiers grouped together somewhere else on the label.
• This is the order of importance of items on the label. Items at the the top of the list should be bigger than those below it.
• 1. Strain name
• 2. Pricing - being per gram the most important of all prices
• 3. THC/CBD percentages
• 4. Strain Type (indica, sativa, hybrid)
• 5. Farm name/logo
• When laying out these labels, they will be going on rounded jars and they will be on display. Think of jars with fancy labels in a candy store. They need to be eye catchy, appealing, but easy read.
• Thank you for all of your hard work, everyone is doing a great job.
• Best,
• Neta

```html
<!DOCTYPE html>
<html lang="en">
<head>
<meta charset="utf-8">
<title>Alder Creek Shiver – Jar Label</title>
<link href="https://fonts.googleapis.com/css2?family=Montserrat:wght@300;400;600;700;800&display=swap" rel="stylesheet">
<style>
  :root {
    --navy: #2d2e7f;
    --mint: #96d4cf;
    --teal: #4ec0b8;
    --leaf-blue: #62b2c9;
    --leaf-soft: #8dcbd3;
  }
  * { margin: 0; padding: 0; box-sizing: border-box; }
  html, body {
    width: 1200px; height: 900px; overflow: hidden; background: #ffffff;
  }
  .label {
    position: relative; width: 1200px; height: 900px; overflow: hidden;
    font-family: "Montserrat", sans-serif; color: var(--navy);
  }
  .label-backdrop { position: absolute; inset: 0; }

  .strain-name {
    position: absolute; left: 133px; top: 92px;
    font-size: 74px; font-weight: 700; line-height: 97px;
    color: var(--mint); letter-spacing: 0.5px;
  }

  .farm-slot {
    position: absolute; left: 0; top: 536px; width: 394px;
    text-align: center; font-size: 40px; font-weight: 300;
    line-height: 53px; color: var(--navy);
  }

  .potency {
    position: absolute; left: 413px; top: 455px;
    font-weight: 700; font-size: 56px; line-height: 88px; color: var(--navy);
  }
  .potency .cbd { padding-left: 42px; }
  .potency sup { font-size: 24px; vertical-align: 26px; margin-right: 6px; }

  .strain-type {
    position: absolute; left: 413px; top: 736px;
    font-size: 50px; font-weight: 600; color: var(--navy);
    text-decoration: underline; text-decoration-thickness: 4px;
    text-underline-offset: 8px;
  }

  .price-list { position: absolute; left: 885px; top: 101px; list-style: none; }
  .price-tier {
    display: flex; align-items: center; height: 138px; margin-bottom: 4px;
  }
  .price-badge {
    width: 138px; height: 138px; border-radius: 50%; background: var(--navy);
    color: var(--mint); display: flex; align-items: center; justify-content: center;
    font-weight: 600; font-size: 52px; letter-spacing: -1px;
  }
  .price-badge.is-primary { font-size: 62px; }
  .price-badge sup { font-size: 24px; vertical-align: 22px; margin-right: 2px; font-weight: 700; }
  .price-unit {
    margin-left: 18px; font-weight: 700; font-size: 24px; color: var(--navy);
  }
  .price-unit.is-primary { font-size: 30px; margin-left: 16px; }
</style>
</head>
<body>
<main class="label">
  <svg class="label-backdrop" width="1200" height="900" viewBox="0 0 1200 900" aria-hidden="true">
    <defs>
      <radialGradient id="leafWash" cx="0.62" cy="0.5" r="0.6">
        <stop offset="0" stop-color="var(--leaf-blue)" />
        <stop offset="0.55" stop-color="var(--leaf-soft)" />
        <stop offset="1" stop-color="var(--mint)" />
      </radialGradient>
    </defs>
    <rect class="name-band" x="0" y="0" width="1200" height="373" fill="var(--navy)" />
    <rect class="farm-panel" x="0" y="373" width="381" height="527" fill="var(--mint)" />
    <rect class="potency-panel" x="381" y="373" width="819" height="527" fill="var(--teal)" />
  </svg>
  <svg class="label-backdrop" width="1200" height="900" viewBox="0 0 1200 900"
       role="img" aria-label="Watercolor cannabis leaf illustration in soft blue tones">
    <circle cx="1190" cy="440" r="485" fill="url(#leafWash)" />
  </svg>

  <h1 class="strain-name">ALDER CREEK<br>SHIVER</h1>

  <p class="farm-slot">FARM<br>LOGO<br>GOES<br>HERE</p>

  <div class="potency">
    <div class="thc">28<sup>%</sup>THC</div>
    <div class="cbd">2<sup>%</sup>CBD</div>
  </div>

  <p class="strain-type">INDICA</p>

  <ul class="price-list">
    <li class="price-tier"><span class="price-badge is-primary"><sup>$</sup>10</span><span class="price-unit is-primary">GRAM</span></li>
    <li class="price-tier"><span class="price-badge"><sup>$</sup>35</span><span class="price-unit">1/8 OZ</span></li>
    <li class="price-tier"><span class="price-badge"><sup>$</sup>70</span><span class="price-unit">1/4 OZ</span></li>
    <li class="price-tier"><span class="price-badge"><sup>$</sup>140</span><span class="price-unit">1/2 OZ</span></li>
    <li class="price-tier"><span class="price-badge"><sup>$</sup>280</span><span class="price-unit">OUNCE</span></li>
  </ul>
</main>
</body>
</html>
```